Wordpress Theme for Larchmont Clinics

** Please view updated Sitemap2.pdf doc to clarify some confusion ***

This is a multiuser WordPress subscription site for Larchmont Clinics. Please see attachment for sitemap. Please do not include extra content like social media icons, search bars, or images. If you have questions, please ask for clarification.
The site contains the following pages and sub-pages:

1. Home
2. Our Clinic
2a. Our Clinic > Mission
2b. Our Clinic > Services
2c. Our Clinic > Clinic Policies
2d. Our Clinic > Schedules
3. Our Staff
3a. Our Staff > [Staff member page]
4. Resources
4a. Resources > Patient Health (index)
4b. Resources > Patient Health (index) > [post]
4c. Resources > Links
4d. Resources > Forms
5. Alerts
5a. Alerts > [Alert Page]
6. Contact Us

Includes the Following Pages, Subpages, and Content
1. Home
a. About Us
b. Our Staff
c. Bulletins
d. Accepting New Patients (shown as an alert widget)
e. Links
i. Physician Toolbox
ii. Book an Appointment
f. Clinic Policies
i. Show first 3 policies (e.g. Late Arrivals, Missed Appointments, Fees)
ii. Link to Clinic Policies page
g. Primary widget (displayed on all pages)
i. Hours of operation
ii. Contact Info
1. Tel
2. Fax
3. Email
4. Address
5. Get directions (link to Google Maps)
2. Our Clinic
a. Main Page
i. Clinic Name
ii. Overview
iii. Languages Spoken
iv. Secondary Navigation
1. Mission
2. Services
3. Clinic Policies
4. Schedules (see attachment)
b. Our Clinic > Mission
c. Our Clinic > Services
i. For each service include service TITLE and DESCRIPTION
d. Our Clinic > Clinic Policies
i. For each policy include policy TITLE and DESCRIPTION
ii. Include the following policies in mockup
1. Late arrivals
2. Missed appointments
3. Fees for missed appointments
4. Referrals and follow-ups
5. Services not covered by RDA
6. Information for LTF patients
7. Medical Legal Reports
e. Our Clinic > Schedules
3. Our Staff
a. Main Page
i. Display a list of staff members. Include NAME and DESIGNATION
b. Our Staff > [Staff Name]
i. Include NAME, PICTURE, DESIGNATION, and BIO
4. Resources
a. Resources > Patient Health
i. Main Page
1. Posts (ordered by date)
a. Title
b. Summary
2. Side Navigation
a. Post Categories
ii. Patient Health > [post title]
1. Title
2. Post Category
3. Date
4. Author
5. Summary
6. Body
b. Resources > Links
1. Secondary Navigation - Categories
a. Sample Categories:
i. Local Services
ii. RDA and Drug Coverage
iii. Mental Health Resources
2. Category page
a. Include the following links in the 'Local Services' category
i. Hypertension clinics
ii. Home Care services
iii. Vaccine Clinics
c. Resources > Forms
i. Display a table with form TITLE and CATEGORY
ii. Side Navigation
1. Form Categories
a. Use the following sample Categories
i. Referrals
ii. Insurance
iii. Intake
iv. Discharge
v. Waivers
5. Alerts
a. Main page
i. List of all Alert posts
1. Include post TITLE as a link to the post
ii. Side Navigation
1. Alerts Archive
a. shown as Month + Number of posts
iii. Alerts > [Alert page]
1. Include TITLE, DATE, AUTHOR, BODY
6. Contact Us
a. Map
b. Hours of operation
c. Address
d. Phone number
e. Fax number
e. Fax number
f. Map
g. Email

Design notes:
- fixed width
- responsive (need designs for mobile, tablet, and desktop)
- simple, dark font, white background
- use Font Awesome icons where needed
- user adds own logo

Target Market(s)

Larchmont Clinics

Industry/Entity Type

Medical

Number of Pages Required

5+ page

Font styles to use
Serif
Sans Serif

Requirements
Must have
• Please keep designs very simple.
• Examples:
• https://www.quolbin.com/install
• http://www.ventrohax.com/company/about-us
• http://brindlequota.org/
• http://www.trosk.com/
Should not have
• Minimal or no use of shadows and gradients

```html
<!DOCTYPE html>
<html lang="en">
<head>
<meta charset="utf-8">
<title>Resources – Forms</title>
<link href="https://fonts.googleapis.com/css2?family=Open+Sans:wght@400;600;700&display=swap" rel="stylesheet">
<style>
:root{
  --blue:#0d8be0;
  --ink:#333333;
  --muted:#555555;
  --band:#f7f7f7;
  --panel:#f3f3f3;
  --line:#dddddd;
  --footer:#262626;
  --footer-text:#8a8a8a;
  --white:#ffffff;
}
*{box-sizing:border-box;margin:0;padding:0}
html,body{width:1200px;height:1110px;overflow:hidden}
body{font-family:"Open Sans",Arial,sans-serif;color:var(--ink);background:var(--white);position:relative;font-size:10px}
a{color:inherit;text-decoration:none}
ul{list-style:none}

.topbar{position:absolute;left:0;top:0;width:1200px;height:30px;background:var(--blue);color:var(--white);font-size:9.5px}
.topbar .left{position:absolute;left:161px;top:9px}
.topbar .right{position:absolute;right:161px;top:9px}
.topbar .sep{display:inline-block;width:1px;height:14px;background:var(--white);vertical-align:middle;margin:0 5px}

.header{position:absolute;left:0;top:30px;width:1200px;height:83px}
.brand{position:absolute;left:162px;top:24px;display:flex;align-items:center;gap:12px;font-size:21px;font-weight:600;color:var(--ink)}
.brand .dot{width:30px;height:30px;border-radius:50%;background:var(--blue)}
.nav{position:absolute;left:0;top:0;height:83px;width:1200px}
.nav a{position:absolute;top:0;height:83px;line-height:83px;font-size:10.5px;color:var(--ink);text-align:center}
.nav a.active{background:var(--blue);color:var(--white)}

.crumbs{position:absolute;left:0;top:113px;width:1200px;height:59px;background:var(--band)}
.crumbs h1{position:absolute;left:162px;top:16px;font-size:10px;font-weight:700}
.crumbs p{position:absolute;left:162px;top:35px;font-size:9.5px}

.forms{position:absolute;left:161px;top:208px;width:652px;height:612px;background:var(--panel);border:1px solid var(--line)}
.box-title{background:var(--blue);color:var(--white);font-weight:700;height:33px;line-height:33px;padding-left:12px}
.forms .box-title{font-size:13px}
.search{position:absolute;left:75px;top:55px;display:flex}
.search input{width:385px;height:36px;border:1px solid #e6e6e6;background:var(--white);font:10px "Open Sans",sans-serif;padding-left:13px;color:var(--muted)}
.search button{width:117px;height:36px;border:0;background:var(--blue);color:var(--white);font:700 10.5px "Open Sans",sans-serif}

.table{position:absolute;left:0;top:114px;width:650px;border-collapse:collapse;font-size:9.5px}
.table th{color:var(--blue);font-weight:600;height:23px;text-align:left;background:var(--panel)}
.table td{height:22.5px}
.table tbody tr:nth-child(odd){background:#f2f2f2}
.table tbody tr:nth-child(even){background:var(--white)}
.table tbody tr.spacer td{height:22px;background:var(--white)}
.table .num{width:75px;text-align:center}
.table .title{width:375px;padding-left:18px;border-left:1px solid #bbb;border-right:1px solid #bbb}
.table .cat{padding-left:19px}

.pager{position:absolute;left:112px;top:563px;display:flex;border:1px solid #ccc;border-radius:3px;background:var(--white)}
.pager a{width:44px;height:29px;line-height:29px;text-align:center;font-size:10px;border-left:1px solid #ccc}
.pager a:first-child{border-left:0;width:38px}
.pager a:last-child{width:38px}

.widget{position:absolute;left:836px;width:203px;border:1px solid var(--line);background:var(--white)}
.widget .box-title{font-size:10.5px;height:34px;line-height:34px}
.cats{top:210px;height:150px}
.cats ul{padding:12px 14px 0}
.cats li{display:flex;justify-content:space-between;height:18px;font-size:9.5px}
.cats li.on{color:var(--blue)}
.hours{top:381px;height:218px;font-size:9.5px}
.hours p{padding:10px 14px 6px;line-height:14px}
.hours li{display:flex;height:18px;padding-left:14px}
.hours li span:first-child{width:90px}
.contact{top:621px;height:150px;font-size:9.5px}
.contact dl{display:grid;grid-template-columns:93px 1fr;padding:12px 14px;row-gap:1px;line-height:15px}

.footer{position:absolute;left:0;top:883px;width:1200px;height:227px;background:var(--footer);border-top:4px solid var(--blue);color:var(--footer-text)}
.footer .brand{left:162px;top:36px;color:var(--white)}
.footer .about{position:absolute;left:162px;top:88px;width:205px;font-size:8.5px;line-height:13.5px;color:#cccccc}
.fcol{position:absolute;top:34px;font-size:9.5px}
.fcol h3{font-size:12.5px;font-weight:600;color:#999;margin-bottom:10px}
.fcol li{height:18px}
.fcol li.current{color:#cccccc}
.fcol dl{display:grid;grid-template-columns:89px 1fr;line-height:15px}
.legal{position:absolute;left:0;top:188px;width:1200px;border-top:1px solid #444;height:35px;font-size:9.5px}
.legal span{position:absolute;top:9px}
</style>
</head>
<body>

<div class="topbar">
  <div class="left">To help Here : 222 333 4444<span class="sep"></span>Email : hello@larchmont.ca</div>
  <div class="right">Book an Appointment<span class="sep"></span>Physician Toolbox</div>
</div>

<header class="header">
  <a class="brand" href="#"><span class="dot"></span>Larchmont Clinics</a>
  <nav class="nav">
    <a href="#" style="left:567px;width:36px">Home</a>
    <a href="#" style="left:636px;width:53px">Our Clinic</a>
    <a href="#" style="left:723px;width:49px">Our Staff</a>
    <a href="#" class="active" style="left:803px;width:60px">Resources</a>
    <a href="#" style="left:894px;width:34px">Alerts</a>
    <a href="#" style="left:961px;width:56px">Contact Us</a>
  </nav>
</header>

<section class="crumbs">
  <h1>RESOURCES</h1>
  <p>HOME / RESOURCES/FORM</p>
</section>

<main class="forms">
  <div class="box-title">FORMS</div>
  <form class="search">
    <input type="text" placeholder="Search forms here...">
    <button type="button">SEARCH</button>
  </form>
  <table class="table">
    <thead><tr><th class="num">#</th><th class="title">Title Name:</th><th class="cat">Category</th></tr></thead>
    <tbody>
      <tr><td class="num">1</td><td class="title">Referrals form1</td><td class="cat">Referrals</td></tr>
      <tr><td class="num">2</td><td class="title">Insurance forms 2</td><td class="cat">Insurance</td></tr>
      <tr><td class="num">3</td><td class="title">Intake forms 5</td><td class="cat">Intake</td></tr>
      <tr><td class="num">4</td><td class="title">Discharge form 1</td><td class="cat">Discharge</td></tr>
      <tr><td class="num">5</td><td class="title">Waivers forms 3</td><td class="cat">Waivers</td></tr>
      <tr><td class="num">6</td><td class="title">Hypertension clinics forms 4</td><td class="cat">Referrals</td></tr>
      <tr><td class="num">7</td><td class="title">Home Care services forms 6</td><td class="cat">Insurance</td></tr>
      <tr><td class="num">8</td><td class="title">Vaccine Clinics form 1</td><td class="cat">Intake</td></tr>
      <tr><td class="num">9</td><td class="title">Referrals form1</td><td class="cat">Discharge</td></tr>
      <tr><td class="num">10</td><td class="title">Insurance forms 2</td><td class="cat">Waivers</td></tr>
      <tr><td class="num">11</td><td class="title">Intake forms 5</td><td class="cat">Referrals</td></tr>
      <tr><td class="num">12</td><td class="title">Discharge form 1</td><td class="cat">Insurance</td></tr>
      <tr><td class="num">13</td><td class="title">Waivers forms 3</td><td class="cat">Intake</td></tr>
      <tr><td class="num">14</td><td class="title">Hypertension clinics forms 4</td><td class="cat">Discharge</td></tr>
      <tr><td class="num">15</td><td class="title">Home Care services forms 6</td><td class="cat">Waivers</td></tr>
      <tr><td class="num">16</td><td class="title">Vaccine Clinics form 1</td><td class="cat">Referrals</td></tr>
      <tr><td class="num">17</td><td class="title">Referrals form1</td><td class="cat">Insurance</td></tr>
      <tr class="spacer"><td class="num"></td><td class="title"></td><td class="cat"></td></tr>
    </tbody>
  </table>
  <nav class="pager">
    <a href="#">&lsaquo;</a><a href="#">1</a><a href="#">2</a><a href="#">3</a><a href="#">4</a><a href="#">5</a><a href="#">6</a><a href="#">7</a><a href="#">8</a><a href="#">&rsaquo;</a>
  </nav>
</main>

<aside class="widget cats">
  <div class="box-title">CATEGORIES</div>
  <ul>
    <li><span>Referrals</span><span>(8)</span></li>
    <li class="on"><span>Insurance</span><span>(20)</span></li>
    <li><span>Intake</span><span>(5)</span></li>
    <li><span>Discharge</span><span>(9)</span></li>
    <li><span>Waivers</span><span>(35)</span></li>
  </ul>
</aside>

<aside class="widget hours">
  <div class="box-title">HOURS OF OPRATION</div>
  <p>Lorem Ipsum is simply dummy text of the printing and typesetting</p>
  <ul>
    <li><span>Monday :</span><span>8:00 AM - 6:00 PM</span></li>
    <li><span>Tuesday :</span><span>8:00 AM - 6:00 PM</span></li>
    <li><span>Wednesday :</span><span>8:00 AM - 6:00 PM</span></li>
    <li><span>Thursday :</span><span>8:00 AM - 6:00 PM</span></li>
    <li><span>Friday :</span><span>8:00 AM - 6:00 PM</span></li>
    <li><span>Saturday :</span><span>9:00 AM - 4:00 PM</span></li>
    <li><span>Sunday :</span><span>9:00 AM - 4:00 PM</span></li>
  </ul>
</aside>

<aside class="widget contact">
  <div class="box-title">CONTACT INFO</div>
  <dl>
    <dt>Telephone :</dt><dd>604-555-0187</dd>
    <dt>Email:</dt><dd>hello@larchmont.ca</dd>
    <dt>Address:</dt><dd>48 Orchard Lane<br>Kelowna,B.<br>Canada, V2K 4R9</dd>
  </dl>
</aside>

<footer class="footer">
  <a class="brand" href="#"><span class="dot"></span>Larchmont Clinics</a>
  <p class="about">Lorem Ipsum is simply dummy text of the printing and typesetting industry. Lorem Ipsum has been the industry's standard dummy text</p>
  <div class="fcol" style="left:461px">
    <h3>Navigation</h3>
    <ul><li class="current">Home</li><li>Our Clinic</li><li>Newsletter</li><li>Our Staff</li><li>Resources</li></ul>
  </div>
  <div class="fcol" style="left:686px">
    <h3>Links</h3>
    <ul><li>Help</li><li>Support</li><li>Privacy Policy</li></ul>
  </div>
  <div class="fcol" style="left:837px">
    <h3>Contact Us</h3>
    <dl>
      <dt>Telephone :</dt><dd>604-555-0187</dd>
      <dt>Email:</dt><dd>hello@larchmont.ca</dd>
      <dt>Address:</dt><dd>48 Orchard Lane<br>Kelowna,B. Canada,<br>V2K 4R9</dd>
    </dl>
  </div>
  <div class="legal">
    <span style="left:162px">© 2015 Larchmont Clinics. All Rights Reservsd</span>
    <span style="left:463px">About Us</span>
    <span style="left:530px">Terms of Use</span>
    <span style="left:615px">Privacy Policy</span>
    <span style="right:164px">Site design &amp; developed by Northgrid Web Studio</span>
  </div>
</footer>

</body>
</html>
```